Brochure for a website accessibility report

This brochure is related to a report that www.qelvantrix.org sell. The report shows the results of an automated audit of a websites accessibility. It shows details of issues found with screen shots, examples of code and provides remediation advice.

The brochure will be a pdf 8.5 inches by 11 inches. It can be anywhere from 6 to 10 pages.

The FlintVue™ name itself should be “Bree Serif” font. The fonts, styles, colors and sizes are up to you.

The images used and logo of the Office of Digital Reachworks and K7P logo are upload

We highlighted in blue page extracts from the report we sell. Do not use the blue highlight, it is merely there to show you where the specific examples of the report we sell are vs the other content in the report. The areas in blue which show the content from the actual report should be shown as an extract of the actual page of the report. You have flexibility to change the layout and the way the content look.

The red square callouts over the blue content are callouts that describe the specific page extracts. We used it as a red callout only so that you would be able to see it. You should change the specific location, look and feel of the callout to be appropriate

Target Market(s)

Marketing and Technical people

Industry/Entity Type

Information Technology

Font styles to use
Sans Serif

Colors

Designer to choose colors to be used in the design.

Requirements
Should not have
• wheelchairs, images of blind people

```html
<!DOCTYPE html>
<html lang="en">
<head>
<meta charset="utf-8">
<title>Accessibility Report Brochure – Spread</title>
<link href="https://fonts.googleapis.com/css2?family=Bree+Serif&family=Open+Sans:wght@400;600;700&family=Montserrat:ital,wght@0,400;1,400&display=swap" rel="stylesheet">
<style>
  :root{
    --bg:#e8e8e8;
    --page-dark:#1b1c1c;
    --page-darker:#141515;
    --green:#35b57a;
    --panel:#c9c9c9;
    --ink:#222;
    --light:#f2f2f2;
    --muted:#bfc4c2;
  }
  *{box-sizing:border-box;margin:0;padding:0}
  html,body{width:1200px;height:1200px;overflow:hidden}
  body{background:var(--bg);font-family:"Open Sans",sans-serif;position:relative}
  .spread{position:absolute;left:40px;top:300px;width:1120px;height:600px;display:flex;box-shadow:0 20px 40px rgba(0,0,0,.25)}
  .page{position:relative;width:560px;height:600px;background:var(--page-dark);overflow:hidden}
  .page--left{border-right:1px solid #0c0c0c}

  .tech-art{position:absolute;border-radius:50%}
  .page--left .tech-art{left:-180px;top:-120px;width:520px;height:520px;
    background:radial-gradient(circle,var(--page-darker) 40%,#3a3d3c 55%,#1b1c1c 60%,#5a5f5d 66%,var(--page-dark) 72%)}
  .page--right .tech-art{right:-230px;top:160px;width:480px;height:480px;
    background:radial-gradient(circle,var(--page-darker) 40%,#3a3d3c 55%,#1b1c1c 60%,#5a5f5d 66%,var(--page-dark) 72%)}

  .brand{position:absolute;top:552px;display:flex;align-items:center;gap:8px;color:var(--light);font-family:"Bree Serif",serif;font-size:13px;line-height:1.05;text-transform:uppercase}
  .brand--left{left:30px}
  .brand--right{right:40px}
  .brand__mark{width:16px;height:16px;background:var(--green)}

  .intro-banner{position:absolute;left:190px;top:18px;width:370px;height:100px;background:var(--green);
    clip-path:polygon(8% 0,100% 0,100% 100%,0 100%);padding:16px 18px 0 46px;
    font-family:"Bree Serif",serif;font-weight:400;color:#fff;font-size:14px;line-height:1.3;text-transform:uppercase}

  .principle{position:absolute;width:190px}
  .principle__label{background:var(--green);color:#fff;font-size:13px;letter-spacing:.05em;padding:5px 12px;border-radius:4px;text-transform:uppercase}
  .principle__label b{margin-right:10px}
  .principle__desc{margin-top:6px;border:1.5px solid var(--muted);border-radius:8px;padding:7px 9px;color:var(--light);font-size:8px;line-height:1.35;background:rgba(20,21,21,.85)}

  .connectors{position:absolute;left:0;top:0}
  .body-copy{position:absolute;left:175px;top:452px;width:300px;color:var(--light);font-size:8px;line-height:1.45}
  .body-copy p+p{margin-top:5px}
  .bottom-band{position:absolute;left:200px;bottom:0;width:360px;height:26px;background:var(--green)}

  .section-band{position:absolute;left:0;top:110px;width:420px;height:120px;background:var(--green);padding:16px 24px}
  .section-band h2{font-family:"Bree Serif",serif;font-weight:400;color:#fff;font-size:24px;text-transform:uppercase}
  .report-extract{position:absolute;left:20px;top:165px;width:380px;background:var(--panel);padding:11px 14px;color:var(--ink);box-shadow:0 3px 8px rgba(0,0,0,.4)}
  .report-extract p{font-size:8.5px;line-height:1.4;margin-bottom:6px}
  .summary-table{width:100%;border-collapse:collapse;font-size:7.5px;line-height:1.3}
  .summary-table th{background:var(--green);color:#fff;font-weight:600;padding:2px 4px;text-align:left;text-transform:uppercase}
  .summary-table td{padding:1px 4px;vertical-align:top;border-bottom:1px solid #b3b3b3}
  .summary-table td.principle-cell{text-transform:uppercase;font-size:7px;color:#444}
  .callout{position:absolute;left:0;top:440px;width:390px;height:92px;background:var(--green);padding:14px 22px;
    font-family:"Montserrat",sans-serif;font-style:italic;color:#fff;font-size:13px;line-height:1.35}
</style>
</head>
<body>
<main class="spread">
  <section class="page page--left">
    <div class="tech-art" role="img" aria-label="Abstract tech circle of white arcs over faint code lines"></div>

    <h1 class="intro-banner">WCAG 2.1 Level A/AA consists of 13 guidelines with 50 checkpoints that are organized under four principles:</h1>

    <svg class="connectors" width="560" height="600" aria-hidden="true">
      <path d="M250 150 H270 V375 H290" fill="none" stroke="var(--green)" stroke-width="1.2"/>
      <path d="M270 255 H300" fill="none" stroke="var(--green)" stroke-width="1.2"/>
      <path d="M250 280 H270" fill="none" stroke="var(--green)" stroke-width="1.2"/>
    </svg>

    <div class="principle" style="left:60px;top:135px">
      <div class="principle__label"><b>1</b>Perceivable</div>
      <div class="principle__desc">Information and user interface components must be presented to users in ways they can perceive. Users must be able to perceive the information being shown.</div>
    </div>
    <div class="principle" style="left:60px;top:262px">
      <div class="principle__label"><b>3</b>Understandable</div>
      <div class="principle__desc">Information and the operation of a user interface must be understandable. Users must be able to understand the content.</div>
    </div>
    <div class="principle" style="left:300px;top:240px">
      <div class="principle__label"><b>2</b>Operable</div>
      <div class="principle__desc">User interface components and navigation must be operable. The interface cannot require interaction a user cannot perform.</div>
    </div>
    <div class="principle" style="left:290px;top:360px;width:200px">
      <div class="principle__label"><b>4</b>Robust</div>
      <div class="principle__desc">Content must be robust enough to be interpreted by a wide variety of user agents, including assistive technologies.</div>
    </div>

    <div class="body-copy">
      <p>Start your journey to a fully compliant website with FlintVue™. This detailed compliance and remediation report is built on our years of experience and proven best practices.</p>
      <p>The FlintVue™ report is designed to be shared with your team. The first section provides an at-a-glance summary chart; the second gives specific examples, suggested fixes and links for detailed training.</p>
    </div>

    <div class="brand brand--left"><span class="brand__mark"></span><span>Office of Digital<br>Reachworks</span></div>
    <div class="bottom-band"></div>
  </section>

  <section class="page page--right">
    <div class="tech-art" role="img" aria-label="Abstract tech circle of white arcs over faint code lines"></div>

    <div class="section-band"><h2>Section 1</h2></div>

    <div class="report-extract">
      <p>The first section of the report begins with a Summary Chart that breaks down WCAG 2.1 A/AA issues by principle:</p>
      <p>EXAMPLE WCAG 2.1 A/AA SUMMARY CHART<br>Checkpoints with failures detected are identified in the “Issues Discovered” column. The detail behind these failures is available in the next section.</p>
      <table class="summary-table">
        <thead><tr><th>Principle</th><th>Guideline</th><th>Issues Discovered</th></tr></thead>
        <tbody>
          <tr><td class="principle-cell" rowspan="4">Perceivable</td><td>Guideline 1.1 Text Alternatives</td><td>1.1.1</td></tr>
          <tr><td>Guideline 1.2 Time-based Media</td><td>1.2.1, 1.2.2, 1.2.3</td></tr>
          <tr><td>Guideline 1.3 Adaptable</td><td>1.3.1, 1.3.2, 1.3.5</td></tr>
          <tr><td>Guideline 1.4 Distinguishable</td><td>1.4.1, 1.4.3, 1.4.4, 1.4.11</td></tr>
          <tr><td class="principle-cell" rowspan="3">Operable</td><td>Guideline 2.1 Keyboard Accessible</td><td>2.1.1, 2.1.2</td></tr>
          <tr><td>Guideline 2.2 Enough Time</td><td>2.2.1, 2.2.2</td></tr>
          <tr><td>Guideline 2.4 Navigable</td><td>2.4.1, 2.4.2, 2.4.4, 2.4.7</td></tr>
          <tr><td class="principle-cell" rowspan="3">Understandable</td><td>Guideline 3.1 Readable</td><td>3.1.1</td></tr>
          <tr><td>Guideline 3.2 Predictable</td><td>3.2.1, 3.2.2</td></tr>
          <tr><td>Guideline 3.3 Input Assistance</td><td>3.3.1, 3.3.2</td></tr>
          <tr><td class="principle-cell">Robust</td><td>Guideline 4.1 Compatible</td><td>4.1.1, 4.1.2</td></tr>
        </tbody>
      </table>
    </div>

    <p class="callout">The report then provides full detail about the specific infractions organized by each of the four principles and explains exactly what the problems are.</p>

    <div class="brand brand--right"><span class="brand__mark"></span><span>Office of Digital<br>Reachworks</span></div>
  </section>
</main>
</body>
</html>
```